PitchTally Webpages and Logo

See attached brief. Take the existing website www.pitchtally.co.uk and logo and transform these assets to:

Give people who arrive on the site for first time the confidence to sign-up easily and quickly
Allow regular returning users quick and easy placing of predictions and encourage them to share the PitchTally prediction on social networks and with their contacts
Convey the essence of a community working together to enjoyably come-up with smart predictions on sporting events
Work seamlessly and well across smartphones, tablets and desktop i.e. Should be Responsive Web Design
Updates

Target Market(s)

Users are sports fans with opinions
Primarily male and early twenties to mid-thirties
They are competitive - they want to beat their peers
Many are from outside the UK

Industry/Entity Type

Events

Logo Text

PitchTally

Coding

Coded - Design and coding required

Number of Pages Required

4 page

Font styles to use
Sans Serif

Requirements
Must have
• Responsive Web Design
• Mobile First
• HTML must work with dedicated bespoke application developed in ASP.NET using MS SQL underneath
• See Brief
Nice to have
• See brief
Should not have
• See brief

```html
<!DOCTYPE html>
<html lang="en">
<head>
<meta charset="utf-8">
<title>PitchTally</title>
<link href="https://fonts.googleapis.com/css2?family=Raleway:wght@400;500;600&family=Open+Sans:ital,wght@0,400;0,600;0,700;1,400&display=swap" rel="stylesheet">
<style>
:root{
  --navy:#073246;
  --navy-dark:#04222f;
  --blue:#1a9ae0;
  --blue-light:#2fb0f0;
  --orange:#fbaa0b;
  --text:#2b2b2b;
  --muted:#7b7b7b;
  --grey-bg:#f5f5f5;
  --tab:#ebebeb;
  --line:#dcdcdc;
  --white:#ffffff;
}
*{margin:0;padding:0;box-sizing:border-box}
html,body{width:780px;height:1200px;overflow:hidden;background:var(--white)}
body{position:relative;font-family:"Open Sans",sans-serif;color:var(--text)}
.abs{position:absolute}
.site-header{left:0;top:0;width:780px;height:61px;background:linear-gradient(180deg,var(--navy),var(--navy-dark))}
.brand{left:62px;top:17px;display:flex;align-items:center;gap:7px;color:var(--white);font-family:"Raleway",sans-serif;font-size:20px;font-weight:500}
.brand-dot{width:22px;height:22px;border-radius:50%;background:var(--blue-light)}
.main-nav{right:80px;top:25px;display:flex;gap:22px;font-family:"Raleway",sans-serif;font-size:11.5px;color:var(--white)}
.hero{left:0;top:61px;width:780px;height:296px;background:linear-gradient(120deg,#b9d3e6 0%,#e8c9a8 35%,#d9a98a 55%,#7fb9e2 80%,#bcd9ef 100%)}
.hero-card{left:59px;top:143px;width:281px;height:131px;background:rgba(255,255,255,.85);border:1px solid rgba(255,255,255,.9);padding:15px 0 0 21px}
.hero-title{font-family:"Raleway",sans-serif;font-size:19px;font-weight:500;color:var(--blue)}
.hero-sub{font-family:"Raleway",sans-serif;font-size:15px;color:var(--text);margin-top:3px}
.hero-text{font-size:7.3px;line-height:13px;color:#333;margin-top:5px;width:240px}
.btn{display:inline-block;width:81px;height:21px;line-height:21px;text-align:center;color:var(--white);font-size:8px;font-weight:700;margin-top:9px;margin-right:3px}
.btn-join{background:var(--orange)}
.btn-more{background:var(--blue)}
.slider-dots{left:370px;top:341px;display:flex;gap:3px}
.slider-dots span{width:9px;height:9px;border-radius:50%;background:var(--white)}
.intro{left:0;top:378px;width:780px;text-align:center}
.intro h1{font-family:"Raleway",sans-serif;font-weight:400;font-size:16px;color:var(--text)}
.intro .lead{font-size:9px;margin-top:3px}
.intro .small{font-size:7.3px;line-height:13px;color:var(--muted);width:600px;margin:9px auto 0}
.stat{top:467px;width:164px;height:87px;border:1px solid var(--line);background:var(--white)}
.stat-head{height:25px;display:flex;justify-content:space-between;align-items:center;padding:0 13px;color:var(--white);font-family:"Raleway",sans-serif;font-size:11.5px;font-weight:500}
.stat-body{height:61px;display:flex;align-items:center;justify-content:center;text-align:center;font-family:"Raleway",sans-serif;font-size:10px;line-height:16px;text-transform:uppercase}
.head-orange{background:linear-gradient(180deg,#ffb513,#f79c05)}
.head-blue{background:linear-gradient(180deg,#33b2f2,#1990dd)}
.head-navy{background:linear-gradient(180deg,#0b3e55,#052636)}
.fixtures{left:0;top:581px;width:780px;height:338px;background:var(--grey-bg);border-top:1px solid #e8e8e8;border-bottom:1px solid #e8e8e8}
.fixtures-tab{left:277px;top:0;width:228px;height:39px;background:var(--tab);clip-path:polygon(0 0,100% 0,88% 100%,12% 100%);text-align:center;line-height:50px;font-family:"Raleway",sans-serif;font-size:16px;color:var(--text)}
.date{width:110px;height:23px;margin-left:-55px;background:var(--white);border:1px solid #e3e3e3;text-align:center;line-height:22px;font-size:7.5px;font-weight:600}
.date::after{content:"";position:absolute;left:50%;bottom:-6px;margin-left:-5px;border:5px solid transparent;border-top-color:var(--white);border-bottom:0}
.crest{width:38px;height:44px;margin-left:-19px;border-radius:4px 4px 19px 19px}
.vs{font-size:10px;color:#555;margin-left:-6px}
.team{width:120px;margin-left:-60px;text-align:center;font-size:7.5px;color:var(--muted)}
.testimonials-title{left:0;top:950px;width:780px;text-align:center;font-family:"Raleway",sans-serif;font-size:18px;color:var(--blue)}
.quote{top:986px;width:240px;height:87px;background:#f7f7f7;border:1px solid #e3e3e3;padding:14px 16px 0;text-align:center;font-style:italic;font-size:7.2px;line-height:12px;color:#555}
.avatar{top:1053px;width:38px;height:38px;border-radius:50%;background:linear-gradient(160deg,#c9a489,#8c6650);border:2px solid var(--white)}
.author{top:1093px;width:200px;text-align:center;font-size:8px;color:#333}
.site-footer{left:0;top:1133px;width:780px;height:67px;background:var(--navy)}
.footer-nav{left:58px;top:20px;font-size:8.8px;color:var(--white)}
.copyright{left:58px;top:38px;font-size:7.2px;color:#8aa3b0}
.social{right:60px;top:22px;display:flex;gap:12px;font-size:9px;font-weight:600;color:var(--white)}
</style>
</head>
<body>
<header class="site-header abs">
  <div class="brand abs"><span class="brand-dot"></span>PitchTally</div>
  <nav class="main-nav abs"><span>Home</span><span>MiniLiga</span><span>Tables</span><span>About</span><span>Kitty</span><span>FAQ</span></nav>
</header>

<section class="hero abs" role="img" aria-label="Photo of a smiling family of football fans cheering in a stadium crowd">
  <div class="hero-card abs">
    <h2 class="hero-title">Vivamus porttitor purus nis</h2>
    <p class="hero-sub">Proin nulla arcu nonummy</p>
    <p class="hero-text">Mauris vel lacus vitae felis vestibulum volutpat Etiam est nunc venenatis in tristique eu imperdiet ac nisl Cum sociis</p>
    <span class="btn btn-join">JOIN NOW</span><span class="btn btn-more">LEARN MORE</span>
  </div>
  <div class="slider-dots abs"><span></span><span></span><span></span><span></span></div>
</section>

<section class="intro abs">
  <h1>Predict results, scores and scorers for your free chance to win a £20</h1>
  <p class="lead">ShopRiver voucher every week. Overall season winner gets up to £1000 in ShopRiver vouchers! No entry fee and no catches.</p>
  <p class="small">Mauris vel lacus vitae felis vestibulum volutpat Etiam est nunc venenatis in tristique eu imperdiet ac nisl Cum sociis natoque penatibus et magnis dis parturient montes nascetur ridiculus mus In iaculis facilisis massa Etiam eu urna Sed porta Suspendisse quam leo molestie sed luctus quis feugiat in pede Fusce tellus Sed me</p>
</section>

<div class="stat abs" style="left:135px"><div class="stat-head head-orange"><span>Results</span><span>100%</span></div><div class="stat-body">Northgate<br>United win</div></div>
<div class="stat abs" style="left:307px"><div class="stat-head head-blue"><span>Score</span><span>50%</span></div><div class="stat-body">Elmford Villa 0<br>Northgate United 2</div></div>
<div class="stat abs" style="left:479px"><div class="stat-head head-navy"><span>1st Goal</span><span>80%</span></div><div class="stat-body">Dalton R</div></div>

<section class="fixtures abs">
  <div class="fixtures-tab abs">TOP TEAM PLAYED</div>

  <div class="date abs" style="left:171px;top:65px">Sat 20 Dec 2014 3:00 PM</div>
  <div class="date abs" style="left:391px;top:65px">Sat 20 Dec 2014 3:00 PM</div>
  <div class="date abs" style="left:609px;top:65px">Sat 20 Dec 2014 3:00 PM</div>

  <div class="crest abs" style="left:118px;top:112px;background:#7fb3dc"></div>
  <div class="vs abs" style="left:172px;top:128px">Vs</div>
  <div class="crest abs" style="left:229px;top:112px;background:#2f5fb0"></div>
  <div class="crest abs" style="left:338px;top:112px;background:#8a2a4e"></div>
  <div class="vs abs" style="left:394px;top:128px">Vs</div>
  <div class="crest abs" style="left:449px;top:112px;background:#d42a20"></div>
  <div class="crest abs" style="left:562px;top:112px;background:#5b79b5"></div>
  <div class="vs abs" style="left:614px;top:128px">Vs</div>
  <div class="crest abs" style="left:668px;top:112px;background:#233a7a"></div>

  <div class="team abs" style="left:118px;top:167px">Northgate City</div>
  <div class="team abs" style="left:229px;top:167px">Glass Harbour</div>
  <div class="team abs" style="left:338px;top:167px">Elmford Villa</div>
  <div class="team abs" style="left:449px;top:167px">Northgate United</div>
  <div class="team abs" style="left:562px;top:167px">Queensway Rovers</div>
  <div class="team abs" style="left:668px;top:167px">Westbury Albion</div>

  <div class="date abs" style="left:171px;top:206px">Sat 20 Dec 2014 3:00 PM</div>
  <div class="date abs" style="left:391px;top:206px">Sat 20 Dec 2014 3:00 PM</div>
  <div class="date abs" style="left:609px;top:206px">Sat 20 Dec 2014 3:00 PM</div>

  <div class="crest abs" style="left:115px;top:242px;background:#1d2a55"></div>
  <div class="vs abs" style="left:169px;top:257px">Vs</div>
  <div class="crest abs" style="left:226px;top:242px;background:#8fc6e6"></div>
  <div class="crest abs" style="left:335px;top:242px;background:#7a2438"></div>
  <div class="vs abs" style="left:391px;top:257px">Vs</div>
  <div class="crest abs" style="left:446px;top:242px;background:#2a4f9c"></div>
  <div class="crest abs" style="left:558px;top:242px;background:#f0a030"></div>
  <div class="vs abs" style="left:611px;top:257px">Vs</div>
  <div class="crest abs" style="left:670px;top:242px;background:#6aa5dc"></div>

  <div class="team abs" style="left:115px;top:302px">Tottenford Athletic</div>
  <div class="team abs" style="left:226px;top:302px">Burnside</div>
  <div class="team abs" style="left:335px;top:302px">Eastham United</div>
  <div class="team abs" style="left:446px;top:302px">Lakecester City</div>
  <div class="team abs" style="left:558px;top:302px">Stripe City</div>
  <div class="team abs" style="left:670px;top:302px">Northgate City</div>
</section>

<h2 class="testimonials-title abs">Testimonials</h2>
<blockquote class="quote abs" style="left:140px">Mauris vel lacus vitae felis vestibulum volutpat Etiam est nunc venenatis in tristique eu imperdiet ac nisl Cum sociis natoque penatibus et magnis dis parturient montes nascetur ridiculus mus In iaculis facilisis massa Etiam eu urna</blockquote>
<blockquote class="quote abs" style="left:400px">Mauris vel lacus vitae felis vestibulum volutpat Etiam est nunc venenatis in tristique eu imperdiet ac nisl Cum sociis natoque penatibus et magnis dis parturient montes nascetur ridiculus mus In iaculis facilisis massa Etiam eu urna</blockquote>
<div class="avatar abs" style="left:240px" role="img" aria-label="Portrait of the first reviewer"></div>
<div class="avatar abs" style="left:500px" role="img" aria-label="Portrait of the second reviewer"></div>
<p class="author abs" style="left:159px">By Author Name</p>
<p class="author abs" style="left:419px">By Author Name</p>

<footer class="site-footer abs">
  <p class="footer-nav abs">Home &nbsp;|&nbsp; MiniLiga &nbsp;|&nbsp; Tables &nbsp;|&nbsp; About &nbsp;|&nbsp; Kitty &nbsp;|&nbsp; FAQ &nbsp;|&nbsp; Sitemap &nbsp;|&nbsp; Contact</p>
  <p class="copyright abs">© 2014 Company Name &nbsp;All right reserved &nbsp;Term of Use</p>
  <div class="social abs"><span>Chatter</span><span>Friendly</span><span>Linkup</span></div>
</footer>
</body>
</html>
```